KV HOLDING Business Cards

I need business cards for "KV Holding group LLC" doublesided... logo on the back (also include logo on front)
logo attached to project... i have jpg up..
Company Info:
827 North Cadwell Avenue, Suite 4B
Chicago, Illinois 60654
facsimile 312-481-2075 (list fax, address, website on all cards.)
www.kvholdinggroup.example
Three different people on cards:
Darnell P. Okafor, CPA MST
Principal
ofc 312-481-3900
mobile 312-204-7751
darnellpokafor@kvholdinggroup.example
Hollis T. Brennecke, CPA MST
Principal
hollistbrennecke@kvholdinggroup.example
mobile 708-539-1184
ofc 312-481-3900
Conrad M Pavlik
Principal
ofc 312-481-3900
no mobile
conradmpavlik@kvholdinggroup.example
I have multiple projects listed.. see below:
Business cards for amber gate ventures llc
letterhead
envelopes
Business cards for KV Holding LLC
letterhead
envelopes
Target Market(s)
rich people
Industry/Entity Type
Business
Look and feel
Each slider illustrates characteristics of the customer's brand and the style your logo design should communicate.

```html
<!DOCTYPE html>
<html lang="en">
<head>
<meta charset="utf-8">
<title>KV Holding Group LLC — Business Card</title>
<link rel="stylesheet" href="https://fonts.googleapis.com/css2?family=Fira+Sans:wght@300;400&display=swap">
<style>
  :root {
    --blue-deep: #0a2a96;
    --blue-mid: #0b4fdc;
    --blue-bright: #1d7bff;
    --navy-mark: #1c3f9e;
    --white: #ffffff;
  }
  * { margin: 0; padding: 0; box-sizing: border-box; }
  html, body {
    width: 1200px;
    height: 777px;
    overflow: hidden;
    background: var(--blue-deep);
  }
  .card {
    position: relative;
    width: 1200px;
    height: 777px;
    overflow: hidden;
    background: radial-gradient(ellipse 70% 80% at 42% 55%, var(--blue-bright) 0%, var(--blue-mid) 45%, var(--blue-deep) 100%);
    font-family: "Fira Sans", sans-serif;
    font-weight: 300;
    color: var(--white);
  }
  .card__facets,
  .card__band {
    position: absolute;
    inset: 0;
    width: 1200px;
    height: 777px;
  }
  .brand-name {
    position: absolute;
    left: 0;
    width: 1200px;
    top: 206px;
    text-align: center;
    font-weight: 400;
    font-size: 38px;
    letter-spacing: 3px;
    color: var(--navy-mark);
  }
  .contact {
    position: absolute;
    font-size: 23px;
    line-height: 30px;
    letter-spacing: 0.2px;
    white-space: nowrap;
  }
  .contact--person { left: 196px; top: 461px; }
  .contact--company { left: 692px; top: 471px; }
  .contact__divider {
    position: absolute;
    left: 668px;
    top: 472px;
    width: 2px;
    height: 131px;
    background: var(--white);
  }
</style>
</head>
<body>
  <main class="card">
    <svg class="card__facets" viewBox="0 0 1200 777" aria-hidden="true">
      <polygon points="270,0 330,0 360,777 250,777" fill="#ffffff" opacity="0.06"/>
      <polygon points="0,300 330,330 280,777 0,777" fill="#3fa0ff" opacity="0.12"/>
      <polygon points="640,0 760,0 700,777 620,777" fill="#ffffff" opacity="0.05"/>
      <polygon points="900,0 1200,0 1200,777 1080,777 800,330" fill="#061c78" opacity="0.35"/>
      <polygon points="800,330 1200,480 1200,777 1080,777" fill="#0a2a96" opacity="0.3"/>
      <polygon points="0,0 200,0 0,180" fill="#0a2a96" opacity="0.35"/>
    </svg>

    <svg class="card__band" viewBox="0 0 1200 777" aria-hidden="true">
      <ellipse cx="590" cy="228" rx="860" ry="106" fill="#ffffff"/>
    </svg>

    <div class="brand-name">KV HOLDING GROUP LLC</div>

    <div class="contact contact--person">
      <p>Darnell P. Okafor, CPA MST</p>
      <p>Principal</p>
      <p>ofc 312-481-3900</p>
      <p>mobile 312-204-7751</p>
      <p>darnellpokafor@kvholdinggroup.example</p>
    </div>

    <div class="contact__divider"></div>

    <div class="contact contact--company">
      <p>827 North Cadwell Avenue, Suite 4B</p>
      <p>Chicago, Illinois 60654</p>
      <p>facsimile 312-481-2075</p>
      <p>www.kvholdinggroup.example</p>
    </div>
  </main>
</body>
</html>
```